BrindleStaffing Business Card Design

We are a staffing company finding positions for dedicated nurses and physicians.

Target Market(s)

Business Professionals

Industry/Entity Type

Staffing

Contact Information for Business Card

Gordon Pratley
Chairman
417 39th Avenue South
SAINT PETERSBURG FL 33712
813-555-4172 Mobile
813-555-8036 Fax
gpratley@brindlestaffing.com
www.brindlestaffing.com

Font styles to use
Sans Serif

Colors
fbee3e
f04a50
f37122

Requirements
Must have
• Logo Attached, see colors below. We'd like to see Yellow, Orange and Red.

```html
<!DOCTYPE html>
<html lang="en">
<head>
<meta charset="utf-8">
<title>BrindleStaffing Business Card</title>
<link rel="stylesheet" href="https://fonts.googleapis.com/css2?family=Open+Sans:wght@400;600;700&display=swap">
<style>
  :root {
    --yellow: #fbee3e;
    --orange: #f37122;
    --red: #f04a50;
    --black: #000000;
    --white: #ffffff;
    --stage-light: #96979b;
    --stage-dark: #3f3e40;
  }
  * { margin: 0; padding: 0; box-sizing: border-box; }
  html, body { width: 1200px; height: 1135px; overflow: hidden; }
  body {
    background: radial-gradient(ellipse 70% 65% at 50% 50%, var(--stage-light), var(--stage-dark));
    font-family: "Open Sans", Arial, sans-serif;
    position: relative;
  }
  .card {
    position: absolute;
    width: 716px;
    height: 408px;
    border-radius: 36px;
    background: var(--black);
    overflow: hidden;
    color: var(--white);
  }
  .card--front { left: 92px; top: 124px; }
  .card--back { left: 368px; top: 606px; }

  .card__swoosh { position: absolute; inset: 0; width: 100%; height: 100%; }

  .holder { position: absolute; right: 42px; top: 32px; text-align: right; }
  .holder__name { font-weight: 700; font-size: 27px; line-height: 1.2; }
  .holder__title { font-weight: 400; font-size: 23px; line-height: 1.25; }

  .wordmark {
    position: absolute;
    display: flex;
    align-items: center;
    gap: 10px;
    font-weight: 700;
    color: var(--yellow);
    letter-spacing: -1px;
    white-space: nowrap;
  }
  .wordmark__dot { width: 14px; height: 14px; border-radius: 50%; background: var(--red); flex: none; }
  .card--front .wordmark { left: 32px; top: 146px; font-size: 50px; }
  .card--back .wordmark { left: 50%; top: 140px; transform: translateX(-50%); font-size: 58px; }

  .contact { position: absolute; left: 32px; top: 279px; list-style: none; }
  .contact__item { display: flex; align-items: center; gap: 11px; height: 30px; font-size: 18px; }
  .contact__icon { width: 16px; height: 16px; flex: none; }

  .divider { position: absolute; left: 322px; top: 312px; width: 1px; height: 50px; background: #8a8a8a; }
  .address { position: absolute; left: 343px; top: 312px; font-size: 18px; line-height: 27px; font-style: normal; }

  .site {
    position: absolute;
    left: 0; right: 0;
    top: 256px;
    text-align: center;
    font-size: 22px;
    letter-spacing: 3px;
  }
  .site__name-a { color: var(--yellow); font-weight: 700; }
  .site__name-b { color: var(--orange); font-weight: 700; }
</style>
</head>
<body>

<section class="card card--front" aria-label="Business card front">
  <svg class="card__swoosh" viewBox="0 0 716 408" preserveAspectRatio="none" aria-hidden="true">
    <path fill="var(--red)" d="M0,68 C60,28 200,28 330,64 C470,104 600,180 716,244 L716,0 L0,0 Z"/>
    <path fill="var(--black)" d="M0,62 C60,22 200,22 330,56 C470,92 600,160 716,222 L716,0 L0,0 Z"/>
    <path fill="var(--orange)" d="M0,58 C60,18 200,18 330,50 C470,86 600,150 716,210 L716,0 L0,0 Z"/>
  </svg>

  <div class="holder">
    <p class="holder__name">Gordon Pratley</p>
    <p class="holder__title">Chairman</p>
  </div>

  <div class="wordmark"><span>BrindleStaffing</span><span class="wordmark__dot"></span></div>

  <ul class="contact">
    <li class="contact__item">
      <svg class="contact__icon" viewBox="0 0 16 16" aria-hidden="true">
        <circle cx="8" cy="8" r="7" fill="none" stroke="var(--yellow)" stroke-width="1.4"/>
        <path d="M5.5 4.5 L7 4.2 L7.6 6.2 L6.7 6.9 C7.2 8 8 8.8 9.1 9.3 L9.8 8.4 L11.8 9 L11.5 10.5 C8 10.8 5.2 8 5.5 4.5Z" fill="var(--yellow)"/>
      </svg>
      <span>813-555-4172</span>
    </li>
    <li class="contact__item">
      <svg class="contact__icon" viewBox="0 0 16 16" aria-hidden="true">
        <rect x="1" y="4" width="14" height="10" fill="var(--yellow)"/>
        <path d="M1 4 L8 9.5 L15 4" fill="none" stroke="var(--black)" stroke-width="1.3"/>
      </svg>
      <span>gpratley@brindlestaffing.com</span>
    </li>
    <li class="contact__item">
      <svg class="contact__icon" viewBox="0 0 16 16" aria-hidden="true">
        <g fill="none" stroke="var(--yellow)" stroke-width="1.2">
          <circle cx="8" cy="8" r="7"/>
          <ellipse cx="8" cy="8" rx="3" ry="7"/>
          <path d="M1 8 H15 M2 4.5 H14 M2 11.5 H14"/>
        </g>
      </svg>
      <span>www.brindlestaffing.com</span>
    </li>
  </ul>

  <div class="divider"></div>
  <address class="address">417 39th avenue south<br>Saint petersburg fl 33712</address>
</section>

<section class="card card--back" aria-label="Business card back">
  <div class="wordmark"><span>BrindleStaffing</span><span class="wordmark__dot"></span></div>
  <p class="site">www.<span class="site__name-a">brindle</span><span class="site__name-b">staffing</span>.com</p>
</section>

</body>
</html>
```